Business Cards for a law firm

Business cards for our law firm. Use our silhoette logo and OAK PARTNERS - check our website (www.oakpartners.example)

Contact Information for Business Card

our silhouette logo, OAK PARTNERS, 800-555-0147, Dorian Pemberton, dorian@oakpartners.example

Requirements
Must have
• our silhouette logo, OAK PARTNERS, 800-555-0147, Dorian Pemberton, dorian@oakpartners.example

```html
<!DOCTYPE html>
<html lang="en">
<head>
<meta charset="utf-8">
<title>Oak Partners — Business Cards</title>
<link rel="stylesheet" href="https://fonts.googleapis.com/css2?family=Montserrat:wght@400;500;700;800&display=swap">
<style>
  :root {
    --navy: #2d3a6b;
    --navy-deep: #222d57;
    --navy-soft: #4a5688;
    --amber: #f7a823;
    --white: #ffffff;
    --stage: #e6e7ea;
  }
  * { box-sizing: border-box; margin: 0; padding: 0; }
  html, body { width: 1200px; height: 900px; overflow: hidden; }
  body {
    background: var(--stage);
    font-family: "Montserrat", Arial, sans-serif;
    position: relative;
  }
  .card {
    position: absolute;
    left: 250px;
    width: 700px;
    height: 400px;
    overflow: hidden;
    background: var(--navy);
    box-shadow: 0 6px 18px rgba(0,0,0,.18);
  }
  .card--front { top: 30px; }
  .card--back { top: 470px; }

  .office-backdrop {
    position: absolute; inset: 0;
    background:
      linear-gradient(180deg, rgba(45,58,107,.2) 0%, rgba(45,58,107,0) 40%, rgba(34,45,87,.35) 100%),
      linear-gradient(100deg, var(--navy-deep) 0%, var(--navy-soft) 45%, var(--navy) 70%, var(--navy-deep) 100%);
    opacity: .9;
  }

  /* Front */
  .front-band {
    position: absolute; left: 0; right: 0; bottom: 0; height: 38px;
    background: var(--amber);
  }
  .front-content {
    position: absolute; top: 42px; left: 0; right: 0;
    display: flex; flex-direction: column; align-items: center; text-align: center;
  }
  .brand-plate {
    display: flex; align-items: center; gap: 14px;
    background: var(--white);
    border-radius: 10px;
    padding: 12px 22px;
  }
  .brand-mark { width: 34px; height: 34px; background: var(--navy); }
  .brand-name {
    font-weight: 800; font-size: 30px; letter-spacing: 3px; color: var(--navy);
  }
  .person-name {
    margin-top: 22px;
    font-weight: 800; font-size: 28px; letter-spacing: 1px; color: var(--amber);
    text-transform: uppercase;
  }
  .contact-list { list-style: none; margin-top: 10px; }
  .contact-list li {
    display: flex; flex-direction: column; align-items: center;
    color: var(--white); font-size: 19px; font-weight: 500; line-height: 1.2;
    margin-top: 4px;
  }
  .contact-icon { width: 16px; height: 16px; fill: var(--amber); margin-bottom: 2px; }

  /* Back */
  .portrait {
    position: absolute;
    background: linear-gradient(180deg, #d7c6b8 0%, #2c3550 38%, #1f2640 100%);
    border-radius: 90px 90px 0 0;
  }
  .portrait--left { left: 20px; top: 190px; width: 170px; height: 210px; }
  .portrait--right { left: 515px; top: 40px; width: 180px; height: 300px; }

  .back-copy {
    position: absolute; left: 190px; top: 50px; width: 320px;
    text-align: center;
  }
  .firm-title {
    font-weight: 800; font-size: 26px; color: var(--amber); letter-spacing: .3px; line-height: 1.1;
    white-space: nowrap;
  }
  .firm-title sup { font-size: 12px; font-weight: 500; }
  .headline {
    margin-top: 8px; color: var(--white); font-weight: 800; font-size: 19px; line-height: 1.3;
  }
  .track-record {
    margin-top: 10px; color: var(--white); font-size: 15px; line-height: 1.35;
  }
  .cta-pill {
    display: inline-block; margin-top: 14px;
    background: var(--amber); color: var(--navy);
    font-weight: 800; font-size: 13px; letter-spacing: .3px;
    padding: 10px 20px; border-radius: 22px;
  }

  .promise-strip { position: absolute; left: 0; bottom: 0; width: 700px; height: 80px; }
  .promise {
    position: absolute; display: flex; align-items: center; gap: 8px;
    color: var(--navy); font-weight: 500; white-space: nowrap; line-height: 1;
  }
  .promise svg { flex: none; }
  .promise--consult { left: 18px; bottom: 10px; height: 20px; font-size: 16px; }
  .promise--nofee { left: 248px; bottom: 18px; height: 30px; font-size: 20px; }
  .promise--visit { left: 558px; bottom: 15px; height: 20px; font-size: 12px; }
</style>
</head>
<body>

<section class="card card--front" aria-label="Business card front">
  <div class="office-backdrop" role="img" aria-label="Faint photo of a modern law office interior in navy tones"></div>
  <div class="front-content">
    <div class="brand-plate">
      <span class="brand-mark"></span>
      <span class="brand-name">OAK PARTNERS</span>
    </div>
    <h1 class="person-name">Dorian Pemberton</h1>
    <ul class="contact-list">
      <li>
        <svg class="contact-icon" viewBox="0 0 24 24" aria-hidden="true"><path d="M6.6 10.8a15 15 0 0 0 6.6 6.6l2.2-2.2a1 1 0 0 1 1-.25 11.4 11.4 0 0 0 3.6.57 1 1 0 0 1 1 1V20a1 1 0 0 1-1 1A17 17 0 0 1 3 4a1 1 0 0 1 1-1h3.5a1 1 0 0 1 1 1c0 1.25.2 2.45.57 3.57a1 1 0 0 1-.25 1z"/></svg>
        800-555-0147
      </li>
      <li>
        <svg class="contact-icon" viewBox="0 0 24 24" aria-hidden="true"><path d="M2 5h20v14H2z M4 7v.5l8 5 8-5V7l-8 5z" fill-rule="evenodd"/></svg>
        dorian@oakpartners.example
      </li>
      <li>
        <svg class="contact-icon" viewBox="0 0 24 24" aria-hidden="true"><circle cx="12" cy="12" r="10"/><path d="M2 12h20M12 2c3 3 3 17 0 20M12 2c-3 3-3 17 0 20" stroke="#2d3a6b" stroke-width="1.4" fill="none"/></svg>
        www.oakpartners.example
      </li>
    </ul>
  </div>
  <div class="front-band"></div>
</section>

<section class="card card--back" aria-label="Business card back">
  <div class="office-backdrop" role="img" aria-label="Faint photo of a modern law office interior in navy tones"></div>
  <div class="portrait portrait--right" role="img" aria-label="Portrait photo of a smiling attorney in a navy suit"></div>
  <div class="portrait portrait--left" role="img" aria-label="Portrait photo of a smiling attorney in a dark suit and patterned tie"></div>

  <div class="back-copy">
    <h2 class="firm-title">THE OAK PARTNERS<sup>®</sup></h2>
    <p class="headline">INJURED?<br>CALL THE OAK PARTNERS!</p>
    <p class="track-record">Over $400,000,000<br>Recovered For Our Clients.</p>
    <span class="cta-pill">GET A FREE CONSULTATION NOW</span>
  </div>

  <svg class="promise-strip" viewBox="0 0 700 80" aria-hidden="true">
    <polygon points="0,40 226,40 222,80 0,80" fill="#f7a823"/>
    <polygon points="238,14 536,8 548,80 232,80" fill="#f7a823"/>
    <polygon points="548,30 700,26 700,80 558,80" fill="#f7a823"/>
  </svg>
  <div class="promise promise--consult">
    <svg width="20" height="20" viewBox="0 0 24 24" aria-hidden="true"><rect x="2" y="3" width="12" height="9" rx="2" fill="none" stroke="#2d3a6b" stroke-width="2"/><circle cx="8" cy="18" r="3" fill="#2d3a6b"/><circle cx="18" cy="16" r="3" fill="#2d3a6b"/></svg>
    Free Consultation
  </div>
  <div class="promise promise--nofee">
    <svg width="30" height="30" viewBox="0 0 30 30" aria-hidden="true"><circle cx="15" cy="15" r="14" fill="#2d3a6b"/><circle cx="15" cy="15" r="9" fill="none" stroke="#f7a823" stroke-width="1.5"/><text x="15" y="19.5" text-anchor="middle" font-size="12" font-weight="700" fill="#f7a823" font-family="Montserrat, sans-serif">$</text></svg>
    No Fee Unless You Win
  </div>
  <div class="promise promise--visit">
    <svg width="18" height="18" viewBox="0 0 24 24" aria-hidden="true"><circle cx="12" cy="12" r="11" fill="#2d3a6b"/><path d="M12 5a4 4 0 0 0-4 4c0 3 4 8 4 8s4-5 4-8a4 4 0 0 0-4-4z" fill="#f7a823"/></svg>
    We'll Come To You
  </div>
</section>

</body>
</html>
```